Every Shelf Set Neatly or ESN Organized needs a business card design. ESN Organized is a professi

We need a business card design that is clean, sharp and conveys a sense of organization. I already have a logo.

Target Market(s)

Families (specifically mothers), small business owners, parents, seniors

Industry/Entity Type

Business

Contact Information for Business Card

My website is www.esnorganized-example.com and my Facebook page is http://www.sociallink-example.com/everyshelfsetneatly. The phone number is 418-552-7094 and I want to be listed as Lorna M. Pelham, Owner

Requirements
Must have
• My logo.

```html
<!DOCTYPE html>
<html lang="en">
<head>
<meta charset="utf-8">
<title>ESN Organized – Business Card</title>
<link rel="stylesheet" href="https://fonts.googleapis.com/css2?family=Roboto:wght@400;500&display=swap">
<style>
  :root {
    --bg: #e9eaec;
    --card-white: #ffffff;
    --card-shade: #e4e4e4;
    --brand-blue: #1a7fdb;
    --ink: #1c1c1c;
    --on-blue: #ffffff;
  }
  * { margin: 0; padding: 0; box-sizing: border-box; }
  html, body { width: 1200px; height: 891px; overflow: hidden; }
  body {
    background: var(--bg);
    display: flex;
    align-items: center;
    justify-content: center;
    gap: 60px;
  }
  .card {
    position: relative;
    width: 530px;
    height: 303px;
    background: radial-gradient(ellipse at 62% 40%, var(--card-white) 0%, #f6f6f6 45%, var(--card-shade) 100%);
    box-shadow: 0 10px 28px rgba(0,0,0,0.18);
    overflow: hidden;
  }
  .rule {
    position: absolute;
    left: 0; right: 0;
    height: 2px;
    background: var(--brand-blue);
  }
  .rule--top { top: 166px; }
  .rule--bottom { top: 262px; }
  .band {
    position: absolute;
    left: 0; right: 0;
    top: 174px;
    height: 82px;
    background: var(--brand-blue);
  }
  .wordmark {
    font-family: "Roboto", sans-serif;
    font-weight: 400;
    color: var(--ink);
    display: flex;
    align-items: center;
    gap: 10px;
    white-space: nowrap;
  }
  .wordmark__mark {
    width: 12px; height: 12px;
    border-radius: 50%;
    background: var(--brand-blue);
  }
  /* back */
  .card--back .wordmark {
    position: absolute;
    left: 0; right: 0;
    top: 174px; height: 82px;
    justify-content: center;
    color: var(--on-blue);
    font-size: 24px;
  }
  .card--back .wordmark__mark { background: var(--on-blue); }
  /* front */
  .card--front .wordmark {
    position: absolute;
    right: 34px;
    top: 68px;
    font-size: 22px;
  }
  .holder {
    position: absolute;
    left: 26px;
    top: 186px;
    color: var(--on-blue);
    font-family: "Roboto", sans-serif;
  }
  .holder__name { font-size: 24px; font-weight: 500; letter-spacing: 0.01em; }
  .holder__role { font-size: 17px; font-weight: 400; margin-top: 4px; padding-left: 52px; }
  .contacts {
    position: absolute;
    left: 250px;
    top: 184px;
    list-style: none;
    font-family: "Roboto", sans-serif;
    font-size: 11px;
    color: var(--on-blue);
  }
  .contacts li { display: flex; align-items: center; gap: 7px; height: 20px; white-space: nowrap; }
  .contacts svg { width: 12px; height: 12px; flex: none; }
</style>
</head>
<body>

  <section class="card card--front" aria-label="Business card front">
    <div class="wordmark"><span class="wordmark__mark"></span>Every Shelf Set Neatly</div>
    <div class="rule rule--top"></div>
    <div class="band"></div>
    <div class="rule rule--bottom"></div>
    <div class="holder">
      <div class="holder__name">Lorna M. Pelham</div>
      <div class="holder__role">Owner</div>
    </div>
    <ul class="contacts">
      <li>
        <svg viewBox="0 0 12 12" aria-hidden="true"><rect width="12" height="12" rx="1.5" fill="#fff"/><path d="M3.5 2.8c.4-.3.9-.2 1.1.2l.6 1.1c.2.3.1.7-.2.9l-.4.3c.4.9 1 1.5 1.9 1.9l.3-.4c.2-.3.6-.4.9-.2l1.1.6c.4.2.5.7.2 1.1l-.5.6c-.4.4-1 .5-1.5.3C5 8.5 3.5 7 2.8 5c-.2-.5-.1-1.1.3-1.5z" fill="#1a7fdb"/></svg>
        418-552-7094
      </li>
      <li>
        <svg viewBox="0 0 12 12" aria-hidden="true"><rect width="12" height="12" rx="1.5" fill="#fff"/><circle cx="6" cy="6" r="3.6" fill="none" stroke="#1a7fdb" stroke-width="1"/><path d="M2.4 6h7.2M6 2.4c-1.4 1.8-1.4 5.4 0 7.2M6 2.4c1.4 1.8 1.4 5.4 0 7.2" fill="none" stroke="#1a7fdb" stroke-width=".8"/></svg>
        www.esnorganized-example.com
      </li>
      <li>
        <svg viewBox="0 0 12 12" aria-hidden="true"><rect width="12" height="12" rx="1.5" fill="#fff"/></svg>
        www.sociallink-example.com/everyshelfsetneatly
      </li>
    </ul>
  </section>

  <section class="card card--back" aria-label="Business card back">
    <div class="rule rule--top"></div>
    <div class="band"></div>
    <div class="rule rule--bottom"></div>
    <div class="wordmark"><span class="wordmark__mark"></span>Every Shelf Set Neatly</div>
  </section>

</body>
</html>
```